Construction company that specializes in roofing and siding

https://maplecrestbuild.example/featured-projects/

https://www.bramwickhomesllc.example/#

https://www.tallgrovecontractors.example/residential-siding-services/

Please model a website after these examples
I posted a doc that has some content to get you started. I will upload more content and photos as the site progresses.

Coded - Design and coding required

5+ page

```html
<!DOCTYPE html>
<html lang="en">
<head>
<meta charset="utf-8">
<title>Stonegate Construction</title>
<link href="https://fonts.googleapis.com/css2?family=Audiowide&family=Lato:wght@400;700&display=swap" rel="stylesheet">
<style>
:root{
  --ink:#222;
  --dark:#2b2b2b;
  --grey:#5a5a5a;
  --nav:#5d5d5d;
  --btn:#5b5b5b;
  --soft:#f4f4f4;
  --line:#cfcfcf;
  --white:#fff;
}
*{box-sizing:border-box;margin:0;padding:0}
html,body{width:1200px;height:4081px;overflow:hidden}
body{font-family:'Lato',sans-serif;color:var(--ink);background:var(--white);position:relative}
.display{font-family:'Audiowide',sans-serif;letter-spacing:1px}
.mark{display:inline-block;width:30px;height:30px;border:4px solid var(--grey);border-radius:50%;vertical-align:middle;margin-right:12px}
.header{height:119px;display:flex;align-items:center;padding:0 110px;justify-content:space-between}
.brand{display:flex;align-items:center;gap:14px}
.brand .dot{width:62px;height:62px;border-radius:50%;background:var(--grey)}
.brand span{font-family:'Audiowide',sans-serif;font-size:24px;color:var(--grey);line-height:1}
.contacts{display:flex;gap:40px;font-family:'Audiowide',sans-serif;font-size:12px}
.contact{display:flex;align-items:center;gap:14px}
.contact small{display:block;font-size:11px;color:var(--grey)}
.nav{height:57px;background:var(--nav);display:flex;justify-content:space-around;align-items:center;padding:0 40px}
.nav a{color:var(--white);font-family:'Audiowide',sans-serif;font-size:15px;text-decoration:none}
.hero{height:490px;position:relative;background:linear-gradient(120deg,#6b7688 0%,#3e4652 45%,#2b3038 100%)}
.hero h1{position:absolute;left:110px;top:90px;color:var(--white);font-size:27px;line-height:47px;font-weight:400}
.btn{display:inline-block;background:var(--btn);color:var(--white);font-family:'Audiowide',sans-serif;font-size:15px;padding:14px 20px;text-decoration:none}
.hero .btn{position:absolute;left:110px;top:292px;background:var(--white);color:var(--ink);padding:16px 20px}
.promise{height:296px;background:var(--soft);text-align:center;padding-top:50px}
h2{font-family:'Audiowide',sans-serif;font-size:33px;color:var(--grey);font-weight:400;text-align:center}
.promise p{font-size:16px;line-height:31px;width:900px;margin:20px auto 0}
.promise .sign{font-size:20px;margin-top:26px}
.photo{position:absolute;width:490px;height:420px}
.sec{position:absolute;left:0;width:1200px}
.txt{font-size:14px;line-height:31px}
.list{list-style:none;margin:8px 0 18px}
.list li{font-size:16px;height:48px;display:flex;align-items:center}
.list .mark{width:24px;height:24px;border-width:3px}
.gutters{position:absolute;left:111px;top:2203px;width:978px;height:244px;background:var(--dark);color:var(--white);text-align:center;padding-top:54px}
.gutters h2{color:var(--white)}
.gutters .mark{border-color:var(--white)}
.gutters p{font-size:14px;line-height:31px;width:760px;margin:22px auto 0}
.about{position:absolute;top:3194px;left:0;width:1200px;height:461px;background:linear-gradient(100deg,#3c3c3c,#6a6a6a 60%,#4d4d4d);color:var(--white);text-align:center;padding-top:52px}
.about h2{color:var(--white)}
.about .mark{border-color:var(--white)}
.about p{font-size:15px;font-weight:700;line-height:31px;width:900px;margin:20px auto 0}
.about .btn{margin-top:44px}
.footer{position:absolute;top:3655px;left:0;width:1200px;height:426px}
.fcol{position:absolute;top:85px}
.fcol h4{font-family:'Audiowide',sans-serif;font-weight:400;font-size:17px;margin-bottom:18px}
.fcol a{display:block;color:var(--ink);text-decoration:none;font-size:14px;line-height:34px;padding-left:4px}
.crow{display:flex;align-items:center;gap:14px;font-size:14px;line-height:26px;margin-bottom:16px}
.ic{width:30px;height:30px;border-radius:50%;background:var(--grey);flex:none}
.social{position:absolute;left:133px;top:226px;display:flex;gap:22px}
.social span{width:24px;height:24px;border-radius:50%;background:var(--grey)}
.rule{position:absolute;left:110px;top:322px;width:980px;border-top:1px solid var(--line)}
.copy{position:absolute;top:356px;width:1200px;text-align:center;font-size:15px;font-weight:700}
</style>
</head>
<body>
<header class="header">
  <div class="brand"><div class="dot"></div><span>STONEGATE<br><small style="font-size:13px">CONSTRUCTION</small></span></div>
  <div class="contacts">
    <div class="contact"><svg width="34" height="30" viewBox="0 0 34 30" fill="none" stroke="#555" stroke-width="2"><rect x="2" y="6" width="30" height="22"/><path d="M2 6l15 12 15-12"/></svg><div><small>SEND US EMAIL</small>INFO@STONEGATE.EXAMPLE</div></div>
    <div class="contact"><svg width="30" height="32" viewBox="0 0 30 32" fill="none" stroke="#555" stroke-width="2"><path d="M15 30s-10-10-10-18a10 10 0 0120 0c0 8-10 18-10 18z"/><circle cx="15" cy="12" r="4"/></svg><div><small>LOCATION</small>STONEGATE, UNITED STATES</div></div>
  </div>
</header>
<nav class="nav"><a href="#">ROOFING ▾</a><a href="#">SIDING ▾</a><a href="#">GUTTERS</a><a href="#">WINDOWS</a><a href="#">REPAIR ▾</a><a href="#">STORM DAMAGE REPAIR ▾</a></nav>
<section class="hero" role="img" aria-label="Dark tiled roof with skylights under a cloudy sky">
  <h1 class="display">STONEGATE CONSTRUCTION<br>IS YOUR SOURCE FOR<br>ROOFING AND SIDING IN<br>MINNESOTA.</h1>
  <a class="btn" href="#">GET STARTED</a>
</section>
<section class="promise">
  <h2><span class="mark"></span>THE STONEGATE PROMISE</h2>
  <p>You deserve timely service, high quality materials, expert installation, and a stonegate warranty. That is what we promise to deliver. I invite you to put us to the test today.</p>
  <p class="sign">Sincerely, Dan Harlow, Owner Stonegate Construction</p>
</section>

<div class="sec" style="top:1010px"><h2><span class="mark"></span>ROOFING</h2></div>
<div class="photo" style="left:109px;top:1108px;background:linear-gradient(135deg,#c9d6de,#6f7478 60%,#3d4a5e)" role="img" aria-label="Two roofers nailing shingles on a roof"></div>
<div class="sec" style="left:662px;top:1124px;width:430px">
  <p class="txt">In MN you should expect to get 20 years of service out of an architectural shingle roof. Shingle manufacturers rate most architectural shingles to last for 30 years. However, this is the longest you should ever go before replacing an architectural shingle roof.</p>
  <ul class="list"><li><span class="mark"></span>Architectural shingles</li><li><span class="mark"></span>Standing seam steel roofing</li><li><span class="mark"></span>Agricultural steel roofing</li></ul>
  <a class="btn" href="#">READ MORE</a>
</div>

<div class="sec" style="top:1598px"><h2><span class="mark"></span>SIDING</h2></div>
<div class="sec" style="left:111px;top:1712px;width:430px">
  <ul class="list" style="margin:0"><li><span class="mark"></span>Vinyl siding</li></ul>
  <p class="txt" style="line-height:27px">Vinyl siding is a great option to give your home's exterior a beautiful makeover. A typical vinyl siding replacement can be completed in 3-5 days and costs about 15-25k.</p>
  <ul class="list" style="margin:4px 0 0"><li><span class="mark"></span>Northline Steel siding</li></ul>
  <p class="txt" style="line-height:27px">Minnesota's own Northline steel siding offers a premium upgrade over vinyl siding. Steel siding will not crack, chip, warp or fade. Northline includes a 35 year warranty against fading and a lifetime warranty against perforation so you can rest assured that your home will be protected for decades to come.</p>
  <a class="btn" href="#" style="margin-top:14px">READ MORE</a>
</div>
<div class="photo" style="left:599px;top:1693px;background:linear-gradient(90deg,#d9b976 0 18%,#9aa4d8 18%,#b8c3e6 70%,#9fb8b8)" role="img" aria-label="Gloved hand hammering a siding panel"></div>

<div class="gutters">
  <h2><span class="mark"></span>GUTTERS</h2>
  <p>We offer 5" or 6" aluminum seamless gutters for your home or business. Gutters are usually an afterthought, but they perform the vital function of carrying water away from your foundation.</p>
</div>

<div class="sec" style="top:2493px"><h2><span class="mark"></span>WINDOWS</h2></div>
<div class="photo" style="left:109px;top:2589px;background:linear-gradient(160deg,#f3ead7,#d9c7a1 50%,#5d7a3e)" role="img" aria-label="Bright room with large black-framed windows"></div>
<div class="sec" style="left:662px;top:2624px;width:430px">
  <p class="txt">At this time, we only offer window replacement as part of a siding replacement job and not as a standalone service. We offer Ashby and Corwin replacement windows. If you are planning on getting your siding replaced, now is the time to consider window replacement. We can help you decide on the right window option for your home. Do you already have an insurance claim for siding replacement? Stonegate Construction can help you utilize your insurance claim to upgrade your windows at the same time.</p>
  <a class="btn" href="#" style="margin-top:14px">READ MORE</a>
</div>
<div class="sec" style="top:3075px;text-align:center"><a class="btn" href="#" style="background:linear-gradient(90deg,#333,#777)">VIEW MORE</a></div>

<section class="about">
  <h2><span class="mark"></span>ABOUT STONEGATE CONSTRUCTION</h2>
  <p>From humble beginnings: In 2016 Dan Harlow started helping people with their home improvement projects. His very first job was installing window trim for a wonderful homeowner in Forest Lake MN. He did his best work and made sure he treated his first customer like family. After all, his first customer was Marie Harlow, his Mom. Today,</p>
  <p>Dan and the Stonegate Construction team are helping homeowners around Minnesota; carrying the spirit of his first job onto every job they touch.</p>
  <a class="btn" href="#">READ MORE</a>
</section>

<footer class="footer">
  <div class="brand" style="position:absolute;left:109px;top:95px"><div class="dot"></div><span>STONEGATE<br><small style="font-size:13px">CONSTRUCTION</small></span></div>
  <div class="social"><span></span><span></span><span></span><span></span></div>
  <div class="fcol" style="left:420px"><h4>QUICK LINKS</h4><a href="#">Home</a><a href="#">Roofing</a><a href="#">Siding</a><a href="#">Gutters</a><a href="#">Contact Us</a></div>
  <div class="fcol" style="left:640px"><h4>HELP LINKS</h4><a href="#">FAQ</a><a href="#">Terms of use</a><a href="#">Privacy Policy</a><a href="#">Support Links</a><a href="#">Conditions</a></div>
  <div class="fcol" style="left:846px"><h4>CONTACT US</h4>
    <div class="crow"><span class="ic"></span><span>Stonegate construction<br>United States</span></div>
    <div class="crow"><span class="ic"></span><span>+1 888 888 8888</span></div>
    <div class="crow"><span class="ic"></span><span>info@stonegatebuild.example</span></div>
  </div>
  <div class="rule"></div>
  <p class="copy">Copyrights@2024.Stonegate construction.All Rights Reserved</p>
</footer>
</body>
</html>
```